Harborview Estates Business Card for Apartment Buildings

Create business cards for resident managers who run apartment buildings. The audience is the public who are searching for apartment rentals, and current residents who live at the apartment building. Key design element will be incorporating the company logo, however, the logo cannot dominate. The building name and manager name are more important than the logo. Current business card design leaves little room for copy, so we may need to reduce the size on the current card to allow for more space for copy.

Target Market(s)

Adults 18-65 years of age, who are looking for an apartment rental, plus current residents who live at our apartment buildings.

Industry/Entity Type

Property Management

Contact Information for Business Card

A major design element will be use of the company logo. Important property and manager contact information must be part of the design. The size of the logo will need to be reduced to make room for building and manager contact copy.

Font styles to use
Sans Serif

Colors
3176b5
000000
959595
ffffff

Requirements
Must have
• 1) Incorporate the company logo.
• 2) Use the company colors (dark blue, black/grey, over white).
• 3) FEATURE THE BUILDING NAME
• 4) FEATURE THE MANAGER NAME
• 5) The company name is less important than BUILDING and MANAGER
• 6) Manager contact information
• **SEE ATTACHED CREATIVE BRIEF**
Nice to have
• 1) Back of card logo watermark
• 2) Ability to write notes on back of carfd
Should not have
• Avoid letting the company logo dominate the card, the building name and manager are more important than the company logo.

```html
<!DOCTYPE html>
<html lang="en">
<head>
<meta charset="utf-8">
<title>Harborview Estates – Resident Manager Business Card</title>
<link href="https://fonts.googleapis.com/css2?family=Work+Sans:wght@400;500;700&display=swap" rel="stylesheet">
<style>
  :root {
    --brand-blue: #3176b5;
    --deep-blue: #1f5f9e;
    --ink: #222222;
    --grey: #959595;
    --paper: #ffffff;
    --card-dark: #3a3b3d;
    --stage: #e9eaec;
  }
  * { box-sizing: border-box; margin: 0; padding: 0; }
  html, body { width: 1200px; height: 900px; overflow: hidden; }
  body {
    background: var(--stage);
    font-family: "Work Sans", Arial, sans-serif;
    position: relative;
  }
  .card {
    position: absolute;
    left: 267px;
    width: 665px;
    height: 380px;
    border-radius: 16px;
    overflow: hidden;
    box-shadow: 0 6px 18px rgba(0,0,0,0.18);
  }
  /* Front */
  .card-front {
    top: 52px;
    background: linear-gradient(135deg, #f1f1f2 0%, var(--paper) 55%);
  }
  .brand {
    position: absolute;
    left: 40px;
    top: 40px;
    display: flex;
    align-items: center;
    gap: 12px;
  }
  .brand-mark {
    width: 28px;
    height: 28px;
    background: var(--brand-blue);
  }
  .brand-name {
    font-weight: 700;
    font-size: 22px;
    color: var(--brand-blue);
    letter-spacing: 0.5px;
    text-transform: uppercase;
  }
  .manager-name {
    position: absolute;
    right: 40px;
    top: 140px;
    font-weight: 500;
    font-size: 28px;
    color: var(--deep-blue);
    text-transform: uppercase;
    letter-spacing: 0.5px;
    line-height: 1;
  }
  .divider {
    position: absolute;
    left: 40px;
    right: 22px;
    top: 180px;
    height: 1px;
    background: var(--brand-blue);
  }
  .accent-bar {
    position: absolute;
    right: 0;
    top: 172px;
    width: 22px;
    height: 46px;
    background: var(--brand-blue);
  }
  .manager-title {
    position: absolute;
    right: 40px;
    top: 190px;
    font-size: 16px;
    line-height: 20px;
    color: var(--ink);
  }
  .contacts {
    position: absolute;
    left: 40px;
    top: 206px;
    list-style: none;
  }
  .contacts li {
    display: flex;
    align-items: center;
    gap: 12px;
    font-size: 17px;
    color: var(--ink);
    line-height: 27px;
  }
  .contacts svg { width: 12px; height: 12px; fill: var(--brand-blue); flex: none; }
  .contacts .web span { color: var(--brand-blue); }
  .property {
    position: absolute;
    right: 40px;
    top: 256px;
    text-align: right;
    font-size: 17px;
    line-height: 25px;
    color: var(--ink);
    font-style: normal;
  }
  /* Back */
  .card-back {
    top: 470px;
    background: var(--card-dark);
    display: flex;
    flex-direction: column;
    align-items: center;
    justify-content: center;
    gap: 28px;
  }
  .back-name {
    font-weight: 700;
    font-size: 40px;
    color: #d9d9d9;
    text-transform: uppercase;
    letter-spacing: 1px;
  }
  .back-web {
    font-size: 18px;
    color: #c9c9c9;
    letter-spacing: 0.5px;
  }
</style>
</head>
<body>
  <section class="card card-front">
    <div class="brand">
      <div class="brand-mark"></div>
      <div class="brand-name">Harborview Estates LLC</div>
    </div>

    <div class="manager-name">Marisol Ortega</div>
    <div class="divider"></div>
    <div class="accent-bar"></div>
    <div class="manager-title">Resident Manager</div>

    <ul class="contacts">
      <li><svg viewBox="0 0 12 12"><path d="M2 0h3l1 3-2 1c.6 1.6 1.8 2.8 3.4 3.4l1-2 3 1v3c0 1-1 1.6-2 1.6C4.8 11 1 7.2 1 2c0-1 .5-2 1-2z"/></svg>555-214-3380</li>
      <li><svg viewBox="0 0 12 12"><path d="M3 0h6a1 1 0 0 1 1 1v10a1 1 0 0 1-1 1H3a1 1 0 0 1-1-1V1a1 1 0 0 1 1-1zm0 2v7h6V2z"/></svg>555-718-4025</li>
      <li><svg viewBox="0 0 12 12"><path d="M1 4h10v5H9v3H3V9H1zM3 0h6v3H3zm1 8v3h4V8z"/></svg>555-602-9174</li>
      <li><svg viewBox="0 0 12 12"><path d="M0 2h12v8H0zm1 1v.3l5 3.4 5-3.4V3z"/></svg>marisol@harborviewest.com</li>
      <li class="web"><svg viewBox="0 0 12 12"><circle cx="6" cy="6" r="6"/></svg><span>www.harborviewest.com</span></li>
    </ul>

    <address class="property">
      <div class="property-name">Cedar Point Apartments</div>
      <div>1482 Linden Avenue</div>
      <div>Fairview, CA 90310</div>
    </address>
  </section>

  <section class="card card-back">
    <div class="back-name">Harborview Estates LLC</div>
    <div class="back-web">www.harborviewest.com</div>
  </section>
</body>
</html>
```